Goodlooking website for a company who is working in the IT consultancy

We want a new website designed in WordPress. You can take www.vantoro.nl as an example. It should be a website with some short blocks of information about the company, nice pictures of our partners and our employees. A job page with a clear filter.

Target Market(s)

B2B

Industry/Entity Type

It Company

Coding

Coded - Design and coding required

Number of Pages Required

5+ page

Font styles to use
Sans Serif

Colors
0455a3
34a7d8

Requirements
Must have
• Check briefing

```html
<!DOCTYPE html>
<html lang="en">
<head>
<meta charset="utf-8">
<title>Our Team – Vantoro</title>
<link href="https://fonts.googleapis.com/css2?family=PT+Sans:wght@400;700&display=swap" rel="stylesheet">
<style>
:root{
  --teal:#3aa9c1;
  --teal-dark:#2c8fa6;
  --slate:#37474f;
  --text:#333;
  --muted:#777;
  --page:#f7f7f7;
  --line:#e3e3e3;
  --footer:#333333;
  --footer-bottom:#3a3a3a;
  --footer-text:#bbb;
  --twitter:#1da1f2;
  --linkedin:#0e76a8;
  --facebook:#3b5998;
}
*{box-sizing:border-box;margin:0;padding:0}
html,body{width:1146px;height:1200px;overflow:hidden}
body{font-family:"PT Sans",sans-serif;background:var(--page);color:var(--text);position:relative}
.site-header{position:absolute;top:0;left:0;width:1146px;height:66px;background:#fff;border-bottom:1px solid var(--line)}
.brand{position:absolute;left:170px;top:10px;display:flex;align-items:center;gap:10px}
.brand-mark{width:46px;height:46px;border-radius:50%;background:var(--teal)}
.brand-name{font-size:30px;font-weight:400;letter-spacing:3px;color:var(--slate)}
.main-nav{position:absolute;right:170px;top:0;display:flex;height:66px}
.main-nav a{display:block;padding:0 18px;line-height:66px;font-size:9px;font-weight:700;color:#777;text-decoration:none;letter-spacing:.3px}
.main-nav a.active{background:var(--teal);color:#fff}
.page-banner{position:absolute;top:67px;left:0;width:1146px;height:92px;background:linear-gradient(90deg,#2f9fc0 0%,#45a8cc 50%,#5c9fc6 100%)}
.page-banner h1{position:absolute;left:170px;top:32px;font-size:22px;font-weight:700;color:#fff}
.breadcrumb{position:absolute;top:159px;left:0;width:1146px;height:37px;background:#f3f3f3;border-bottom:1px solid var(--line);padding-left:170px;line-height:37px;font-size:10px;font-weight:700;letter-spacing:.5px;color:#444}
.team-card{position:absolute;width:250px;height:268px;background:#fafafa;box-shadow:0 0 4px rgba(0,0,0,.12);text-align:center}
.avatar{width:123px;height:123px;border-radius:50%;margin:28px auto 0;background:radial-gradient(circle at 50% 40%,#cfcfcf,#8d8d8d)}
.member-name{margin-top:25px;font-size:13px;font-weight:700;color:#333}
.member-role{margin-top:8px;font-size:9.5px;color:#777}
.socials{margin-top:20px;display:flex;justify-content:center;gap:4px}
.socials span{width:18px;height:18px;border-radius:50%}
.socials .s1{background:var(--twitter)}.socials .s2{background:var(--linkedin)}.socials .s3{background:var(--facebook)}
.join-card{position:absolute;left:706px;top:513px;width:250px;height:268px;background:var(--slate);text-align:center;color:#fff;padding-top:78px}
.join-card h2{font-size:17px;font-weight:700}
.join-card p{margin-top:14px;font-size:11px;line-height:17px;color:#c9d1d5}
.btn-contact{display:inline-flex;align-items:center;gap:5px;margin-top:14px;background:var(--teal);color:#fff;font-size:9.5px;font-weight:700;letter-spacing:.5px;padding:10px 14px;border-radius:16px;box-shadow:0 2px 0 #5fc2d6}
.site-footer{position:absolute;top:805px;left:0;width:1146px;height:315px;background:var(--footer);color:var(--footer-text)}
.footer-col{position:absolute;top:56px}
.footer-col h3{font-size:13px;font-weight:400;letter-spacing:1px;color:#fff;padding-bottom:9px;border-bottom:1px solid #555;position:relative}
.footer-col h3::after{content:"";position:absolute;left:0;bottom:-1px;width:32px;height:2px;background:var(--teal)}
.contact-item{position:relative;padding-left:24px;margin-top:22px;font-size:10.5px;letter-spacing:.6px;line-height:16px}
.contact-item svg{position:absolute;left:0;top:2px}
.contact-item b{font-weight:400;color:#fff;display:block;margin-bottom:4px}
.contact-item .big{font-size:14px}
.contact-item .mail{font-size:14px;color:var(--teal)}
.link-list{list-style:none;margin-top:12px}
.link-list li{font-size:10.5px;letter-spacing:.8px;padding:8px 0 8px 20px;border-bottom:1px solid #3f3f3f;position:relative}
.link-list li::before{content:"»";position:absolute;left:2px;color:#888}
.link-list li:last-child{border-bottom:none}
.newsletter p{margin-top:25px;font-size:10px;color:#999}
.newsletter .email-field{margin-top:15px;width:212px;height:28px;background:#fff;border:1px solid #ccc;font-size:10px;color:#999;padding-left:10px;line-height:26px}
.btn-subscribe{margin-top:8px;display:inline-flex;align-items:center;gap:7px;background:#444;color:#fff;font-size:10.5px;padding:8px 16px;border-radius:15px}
.footer-bottom{position:absolute;top:1120px;left:0;width:1146px;height:80px;background:var(--footer-bottom);border-top:1px solid #444;text-align:center}
.footer-social{display:flex;justify-content:center;gap:4px;margin-top:15px}
.footer-social span{width:30px;height:30px;border-radius:50%;border:1px solid #666}
.copyright{margin-top:10px;font-size:9.5px;letter-spacing:.8px;color:#999}
</style>
</head>
<body>
<header class="site-header">
  <div class="brand"><span class="brand-mark"></span><span class="brand-name">VANTORO</span></div>
  <nav class="main-nav">
    <a href="#">HOME</a><a href="#">OUR SOLUTIONS</a><a href="#" class="active">OUR TEAM</a><a href="#">JOBS</a><a href="#">CONTACT</a>
  </nav>
</header>
<section class="page-banner" role="img" aria-label="Banner photo of glass office towers in blue tones"><h1>Our Team</h1></section>
<div class="breadcrumb">Home &gt; Our Team</div>

<article class="team-card" style="left:170px;top:221px">
  <div class="avatar" role="img" aria-label="Portrait photo of Jeroen Bakker"></div>
  <div class="member-name">Jeroen Bakker</div><div class="member-role">Director</div>
  <div class="socials"><span class="s1"></span><span class="s2"></span><span class="s3"></span></div>
</article>
<article class="team-card" style="left:438px;top:221px">
  <div class="avatar" role="img" aria-label="Portrait photo of Sander Mulder"></div>
  <div class="member-name">Sander Mulder</div><div class="member-role">Mission Critical Engineer</div>
  <div class="socials"><span class="s1"></span><span class="s2"></span><span class="s3"></span></div>
</article>
<article class="team-card" style="left:706px;top:221px">
  <div class="avatar" role="img" aria-label="Portrait photo of Peter Verbeek"></div>
  <div class="member-name">Peter Verbeek</div><div class="member-role">Consultant</div>
  <div class="socials"><span class="s1"></span><span class="s2"></span><span class="s3"></span></div>
</article>
<article class="team-card" style="left:170px;top:513px">
  <div class="avatar" role="img" aria-label="Portrait photo of Thijs van Dam"></div>
  <div class="member-name">Thijs van Dam</div><div class="member-role">Mission Critical Engineer</div>
  <div class="socials"><span class="s1"></span><span class="s2"></span><span class="s3"></span></div>
</article>
<article class="team-card" style="left:438px;top:513px">
  <div class="avatar" role="img" aria-label="Portrait photo of Erik Hoogendoorn"></div>
  <div class="member-name">Erik Hoogendoorn</div><div class="member-role">Mission Critical Engineer</div>
  <div class="socials"><span class="s1"></span><span class="s2"></span><span class="s3"></span></div>
</article>
<aside class="join-card">
  <h2>Join our team</h2>
  <p>We are looking for enthusiastic<br>knowledgeable colleagues!</p>
  <span class="btn-contact">CONTACT US
    <svg width="9" height="9" viewBox="0 0 10 10"><circle cx="5" cy="5" r="4" fill="none" stroke="#fff" stroke-width="1.4"/><path d="M3 5h4M5.5 3.5 7 5 5.5 6.5" fill="none" stroke="#fff" stroke-width="1.2"/></svg>
  </span>
</aside>

<footer class="site-footer">
  <div class="footer-col" style="left:191px;width:169px">
    <h3>Contact Info</h3>
    <div class="contact-item" style="margin-top:24px">
      <svg width="10" height="13" viewBox="0 0 10 13"><path d="M5 0a5 5 0 0 1 5 5c0 3.5-5 8-5 8S0 8.5 0 5a5 5 0 0 1 5-5z" fill="#3aa9c1"/><circle cx="5" cy="5" r="1.8" fill="#333"/></svg>
      <b>Address:</b>Lindelaan 14,<br>3521 AB Utrecht
    </div>
    <div class="contact-item">
      <svg width="11" height="12" viewBox="0 0 11 12"><path d="M2 0l2.5 3-1.3 1.5c.8 1.8 2 3 3.7 3.8L8.3 7 11 9.5 9.5 12C4.5 11 0 6.5 0 1.5z" fill="#3aa9c1"/></svg>
      <b>Phone:</b><span class="big">030-1234567</span>
    </div>
    <div class="contact-item">
      <svg width="14" height="10" viewBox="0 0 14 10"><rect width="14" height="10" fill="#3aa9c1"/><path d="M0 0l7 5 7-5" fill="none" stroke="#333" stroke-width="1.2"/></svg>
      <b>Email:</b><span class="mail">info@vantoro.nl</span>
    </div>
  </div>
  <div class="footer-col" style="left:402px;width:123px">
    <h3>Quick Links</h3>
    <ul class="link-list"><li>Home</li><li>Our Solutions</li><li>Our Team</li><li>Jobs</li><li>Contact</li></ul>
  </div>
  <div class="footer-col" style="left:567px;width:132px">
    <h3>Support</h3>
    <ul class="link-list"><li>Terms of Use</li><li>Privacy Policy</li><li>Cookie Policy</li></ul>
  </div>
  <div class="footer-col newsletter" style="left:740px;width:214px">
    <h3>Join Our Newsletter</h3>
    <p>Subscribe for Job Alerts and Updates!</p>
    <div class="email-field">Enter Your Email</div>
    <span class="btn-subscribe"><svg width="11" height="11" viewBox="0 0 11 11"><path d="M11 0 0 5l4 1.5L5 11z" fill="#fff"/></svg>Subscribe</span>
  </div>
</footer>
<div class="footer-bottom">
  <div class="footer-social"><span></span><span></span></div>
  <div class="copyright">Copyright © 2018 VANTORO. All Rights Reserved.</div>
</div>
</body>
</html>
```